Business Card - high end, modern health care

Hey designers!

We need a double sided business card for the boutique, cutting edge physical therapy rehabilitation centre in Sydney's Northern Beaches.

With the most qualified physios in the area The Harbourview Motion Clinic does what other physiotherapy practices do not, we take our time with our patients giving them longer appointments, better physios and therefor faster results!

We guarantee that the service people receive at THMC will be unparalleled.

Hence we need a business card to reflect our modern, boutique, high end service. The final design needs to reflect that we are in a class of our own yet with the feel of beachside retreat.

Below I have attached our logo in both blue on white and white on blue. The exact colour is;
and the font that we have used in our logo is Tex Gyre Aventador.

I like the idea of the blue as the main colour as it is more eye catching and our signage onto the main road will be in this blue and in the interest of consistency across marketing the blue needs to be a part of the design. However I would appreciate a few designs onto a wooden background as this is a visual theme within the fitout of the practice.

The design needs to be of standard size (91x55mm).

Target Market(s)

We target people who have an end outcome in mind and those who have had poor experiences with other providers and ensure that everyone gets the care that they deserve with a premium service that is tailored to the individuals circumstances. As a premium service, the target market is highly educated, business and tech savvy with the additional target market of elderly people who have self funded their retirement and see value in paying for the best ongoing rehabilitation to maintain independence.

Industry/Entity Type

Physical Therapy

Contact Information for Business Card

Name, designation( Titled Musculoskeletal Physiotherapist... there will also be those in the company that have multiple designations ie 5 or 6 words long), phone number, email, facebook, instagram, address

Font styles to use
Sans Serif

Colors

Designer to choose colors to be used in the design.

Requirements
Must have
• Front - The logo as large as possible, blue or wooden theme, and all of the important details.
• Back - A blank space/lines on which to write appointment times (no "Appointment, date, time" etc.)
Nice to have
• facebook url
• logos for facebook and instagram
• Mini logos for the phone and email?

```html
<!DOCTYPE html>
<html lang="en">
<head>
<meta charset="utf-8">
<title>The Harbourview Motion Clinic – Business Card</title>
<link href="https://fonts.googleapis.com/css2?family=Montserrat:wght@500;700&display=swap" rel="stylesheet">
<style>
  :root {
    --brand-blue: #0b55a6;
    --brand-blue-deep: #0a4a92;
    --ink: #3a3d42;
    --paper: #ffffff;
    --paper-shade: #eceef1;
    --rule-grey: #8c9096;
    --stage: #e4e6ea;
  }
  * { margin: 0; padding: 0; box-sizing: border-box; }
  html, body { width: 1200px; height: 900px; overflow: hidden; }
  body {
    background: var(--stage);
    font-family: "Montserrat", Arial, sans-serif;
    display: flex; flex-direction: column; align-items: center; justify-content: center;
    gap: 40px;
  }
  .card {
    position: relative; width: 660px; height: 399px;
    border-radius: 18px; overflow: hidden;
    box-shadow: 0 10px 30px rgba(0,0,0,.18);
  }

  /* Front */
  .card--front { background: linear-gradient(135deg, var(--paper) 40%, var(--paper-shade) 100%); }
  .wordmark { position: absolute; display: flex; align-items: center; gap: 14px; font-weight: 700; color: var(--brand-blue); }
  .wordmark__dot { width: 40px; height: 40px; border-radius: 50%; background: currentColor; flex: none; }
  .wordmark__name { line-height: 1.05; text-transform: uppercase; }
  .wordmark__line1 { display: block; font-size: 27px; letter-spacing: .5px; }
  .wordmark__line2 { display: block; font-size: 15px; letter-spacing: 5px; margin-top: 3px; }
  .card--front .wordmark { left: 40px; top: 38px; }

  .contact-list { position: absolute; left: 40px; top: 110px; list-style: none; font-size: 13.5px; color: var(--ink); font-weight: 500; }
  .contact-list li { display: flex; align-items: center; gap: 9px; margin-bottom: 7px; }
  .contact-list svg { width: 13px; height: 13px; fill: none; stroke: var(--brand-blue); stroke-width: 2; flex: none; }
  .contact-list .web-accent { color: var(--brand-blue); }

  .divider { position: absolute; left: 40px; top: 248px; width: 470px; height: 2px; background: var(--brand-blue); }
  .divider-block { position: absolute; right: 0; top: 232px; width: 130px; height: 24px; background: var(--brand-blue); }

  .person { position: absolute; right: 150px; top: 188px; text-align: right; }
  .person__name { font-size: 24px; font-weight: 700; color: var(--brand-blue); text-transform: uppercase; letter-spacing: .5px; }
  .person__title { font-size: 14px; font-weight: 500; color: var(--ink); margin-top: 3px; }

  .address { position: absolute; right: 150px; top: 262px; text-align: right; font-size: 13.5px; font-weight: 500; color: var(--ink); line-height: 1.5; }

  .swoosh { position: absolute; left: 0; bottom: 0; width: 100%; height: 100%; }

  /* Back */
  .card--back { background: var(--paper); }
  .back-band { position: absolute; left: 0; top: 0; width: 100%; height: 45%; background: linear-gradient(135deg, var(--brand-blue) 0%, var(--brand-blue-deep) 100%); }
  .card--back .wordmark { color: var(--paper); left: 40px; top: 52px; }
  .card--back .wordmark__dot { width: 56px; height: 56px; }
  .card--back .wordmark__line1 { font-size: 38px; }
  .card--back .wordmark__line2 { font-size: 21px; letter-spacing: 7px; }
  .appt-label { position: absolute; left: 40px; top: 196px; font-size: 18px; font-weight: 500; color: var(--brand-blue); letter-spacing: .5px; }
  .appt-lines { position: absolute; left: 40px; right: 40px; top: 250px; }
  .appt-lines span { display: block; height: 1px; background: var(--rule-grey); margin-bottom: 44px; }
</style>
</head>
<body>

  <section class="card card--front" aria-label="Business card front">
    <svg class="swoosh" viewBox="0 0 660 399" preserveAspectRatio="none" aria-hidden="true">
      <path d="M0 318 C180 312 380 340 600 399 L0 399 Z" fill="var(--brand-blue)"/>
      <path d="M60 345 C230 340 400 362 560 399" fill="none" stroke="var(--paper)" stroke-width="3"/>
    </svg>

    <div class="wordmark">
      <span class="wordmark__dot"></span>
      <span class="wordmark__name">
        <span class="wordmark__line1">The Harbourview</span>
        <span class="wordmark__line2">Motion Clinic</span>
      </span>
    </div>

    <ul class="contact-list">
      <li><svg viewBox="0 0 16 16"><path d="M4 1.5 L6.5 4.5 L5 6.5 C6 8.5 7.5 10 9.5 11 L11.5 9.5 L14.5 12 L12.5 14.5 C7 14 2 9 1.5 3.5 Z"/></svg><span>+61 2 5550 1427</span></li>
      <li><svg viewBox="0 0 16 16"><rect x="1.5" y="3.5" width="13" height="9" rx="1"/><path d="M1.5 4 L8 9 L14.5 4"/></svg><span>info@harbourviewmotion.com</span></li>
      <li><svg viewBox="0 0 16 16"><circle cx="8" cy="8" r="6.5"/><path d="M1.5 8 H14.5 M8 1.5 C5 5 5 11 8 14.5 M8 1.5 C11 5 11 11 8 14.5"/></svg><span>www.<span class="web-accent">harbourviewmotion</span>.com</span></li>
    </ul>

    <div class="person">
      <p class="person__name">Daniel Ashford</p>
      <p class="person__title">Director</p>
    </div>
    <div class="divider"></div>
    <div class="divider-block"></div>

    <p class="address">48 Tidewater Road, Unit 3,<br>Shoreline City, PO 20417</p>
  </section>

  <section class="card card--back" aria-label="Business card back">
    <div class="back-band"></div>
    <div class="wordmark">
      <span class="wordmark__dot"></span>
      <span class="wordmark__name">
        <span class="wordmark__line1">The Harbourview</span>
        <span class="wordmark__line2">Motion Clinic</span>
      </span>
    </div>
    <p class="appt-label">Appointment</p>
    <div class="appt-lines"><span></span><span></span><span></span></div>
  </section>

</body>
</html>
```